Pinecrest Harbor Foundation Web Design

The design we need is for a WordPress blog that will be our content platform. We are a registered 501(c)3 non-profit that focuses on financially supporting the treatment of cancer patients that have been told they have no hope and there is nothing the conventional medical system can do for them. Through this wesbite we want to both rasie awareness about the treatment options plus, raise funds for treating patients. The two primary target audiences of the site are...

1. Terminally ill patients and their families to let them know that there is an option other then hospice and that we are hear to support that option.

2. People looking to help donate to a worthwhile cause that resonates with them.

The website is https://pinecrestharborfoundation.org/

See attached logo designs!!!

Target Market(s)

Cancer patients and their families

Industry/Entity Type

Foundation

Font styles to use
Sans Serif

Colors
ffffff
fbed22

Requirements
Must have
• I like this look of this site. It is clean, simple, helpful, soft. I like the flow of the pages.
• http://www.meadowsforcalm.org/
• I like the design and flow but NOT the color or boldness
• https://tvbn-youth.org/
• I like this style for a donation page.
• https://www.tumorstudyhub.org/we-are-tsh/join-the-cause/donations/one-time-donation
• with the addition of a Would you like your employer to match? button.
Nice to have
• White black and gold - but soft
• Even possibly grayscale like the site I like.

```html
<!DOCTYPE html>
<html lang="en">
<head>
<meta charset="utf-8">
<title>Pinecrest Harbor Foundation</title>
<link href="https://fonts.googleapis.com/css2?family=Open+Sans:wght@300;400;600;700&family=Roboto:wght@400&display=swap" rel="stylesheet">
<style>
:root{
  --gold:#efc75a;
  --gold-dark:#e2b84a;
  --ink:#1e1e1e;
  --text:#4a4a4a;
  --muted:#777;
  --link-blue:#1c64a3;
  --label-blue:rgba(40,118,190,.85);
  --field:#efefef;
  --field-line:#d6d6d6;
  --footer:#c6c6c6;
  --white:#ffffff;
}
*{margin:0;padding:0;box-sizing:border-box}
html,body{width:1200px;height:2917px;overflow:hidden}
body{position:relative;background:var(--white);font-family:"Open Sans",Arial,sans-serif;color:var(--text)}
.abs{position:absolute}

/* Hero */
.hero{left:0;top:0;width:1200px;height:661px;
  background:radial-gradient(ellipse at 62% 40%,#e8dccd 0%,#d9d4cc 28%,transparent 55%),
  linear-gradient(100deg,#e9ecef 0%,#dfe6ea 35%,#cfdfe6 60%,#bcd6e2 80%,#a8cad9 100%)}
.brand{left:130px;top:34px;display:flex;align-items:center;gap:14px}
.brand-dot{width:46px;height:46px;border-radius:50%;background:var(--gold)}
.brand-name{font-weight:700;font-size:19px;color:var(--ink);line-height:1.15;width:190px}
.nav{right:130px;top:20px;display:flex;gap:8px}
.nav a{font-size:11px;font-weight:600;color:var(--ink);text-decoration:none;padding:6px 10px;letter-spacing:.2px}
.nav a.active{background:var(--gold)}
.hero-title{left:152px;top:270px;font-weight:300;font-size:43px;line-height:46px;color:var(--ink)}
.btn-dark{left:158px;top:389px;width:105px;height:37px;background:#111;color:var(--white);font-size:11px;font-weight:700;display:flex;align-items:center;justify-content:center}
.dots{left:566px;top:623px;display:flex;gap:6px}
.dots span{width:10px;height:10px;border-radius:50%;background:#444}
.dots span.on{background:#e3673a}

/* Headings */
.section-title{width:1200px;left:0;text-align:center;font-weight:700;font-size:25px;color:var(--gold)}
.mission-text{left:330px;top:778px;width:542px;text-align:center;font-family:"Roboto",Arial,sans-serif;font-size:12.5px;line-height:15.5px;color:#333}
.btn-gold{background:var(--gold);color:var(--white);font-weight:700;display:flex;align-items:center;justify-content:center}
.give{left:510px;top:898px;width:180px;height:40px;font-size:13px}

/* Stars */
.star{width:298px;height:224px}
.star-label{position:absolute;left:0;top:172px;width:117px;height:27px;background:var(--label-blue);color:var(--white);font-size:10px;font-weight:700;padding-left:10px;display:flex;align-items:center}
.p1{background:linear-gradient(160deg,#3c4a45,#5e5a50 50%,#27312e)}
.p2{background:linear-gradient(160deg,#2c4a2e,#6d8f56 50%,#8fb07a)}
.p3{background:linear-gradient(160deg,#e7dcc0,#b79a7e 50%,#c63648)}
.p4{background:linear-gradient(160deg,#eceeee,#c9c4bd 50%,#f4f4f4)}
.p5{background:linear-gradient(160deg,#6a6e80,#8a7563 50%,#5fa440)}
.p6{background:linear-gradient(160deg,#f3f3f3,#d8c8bd 50%,#8f2a2f)}

/* Events */
.col-title{font-weight:700;font-size:19px;color:var(--gold)}
.divider-v{left:624px;top:1614px;width:1px;height:506px;background:#ddd}
.event{left:173px;width:400px;height:130px}
.date{position:absolute;left:0;top:0;width:43px;height:54px;background:var(--gold);color:var(--white);text-align:center;font-weight:700}
.date .m{font-size:8px;display:block;padding-top:4px}
.date .d{font-size:17px;display:block;line-height:20px}
.date .y{font-size:7px;display:block}
.event h3{position:absolute;left:86px;top:0;width:290px;font-size:13px;line-height:17px;color:var(--link-blue);font-weight:700}
.event p{position:absolute;left:86px;top:42px;width:300px;font-size:11.5px;line-height:16px;color:var(--muted)}
.event .more{position:absolute;left:88px;top:85px;width:75px;height:20px;font-size:8px}

.field{left:704px;width:333px;height:47px;background:var(--field);border:1px solid var(--field-line);font-size:11px;color:#555;padding-left:22px;display:flex;align-items:center}
.submit{left:706px;top:1890px;width:107px;height:47px;font-size:12px}

/* Donate */
.donate{left:0;top:2165px;width:1200px;height:460px;
  background:radial-gradient(ellipse at 26% 45%,#c9a68f 0%,#a78b6f 14%,transparent 30%),
  linear-gradient(90deg,#2f4a22 0%,#5b7f3b 25%,#38562a 50%,#2c3f22 75%,#243419 100%)}
.donate-title{left:650px;top:2254px;font-size:39px;font-weight:400;color:var(--white)}
.donate-text{left:655px;top:2322px;width:345px;font-family:"Roboto",Arial,sans-serif;font-size:13.5px;line-height:20px;color:var(--white)}
.donate-btn{left:654px;top:2453px;width:167px;height:47px;font-size:15px;color:#222}
.wave{left:0;top:2520px}

/* Footer */
.footer{left:0;top:2600px;width:1200px;height:317px;background:var(--footer)}
.foot-title{font-size:11px;font-weight:700;color:var(--ink)}
.foot-line{font-size:11px;color:#333;line-height:14px}
.menu{left:461px;top:2680px;list-style:none;font-size:11px;color:#333;line-height:19.5px}
.ico{left:138px}
.news-input{left:617px;top:2676px;width:186px;height:35px;background:var(--white);font-size:10px;color:#444;padding-left:12px;display:flex;align-items:center}
.signup{left:620px;top:2731px;width:94px;height:33px;font-size:11px;color:#333}
.social{left:897px;top:2680px;display:flex;gap:12px}
.social span{width:33px;height:33px;border-radius:50%}
.divider-h{left:132px;top:2830px;width:934px;height:1px;background:#aaa}
.copy{left:0;top:2866px;width:1200px;text-align:center;font-size:11px;color:#333}
</style>
</head>
<body>

<section class="abs hero" role="img" aria-label="Photo of a young girl in a knitted cap hugging a soft toy bunny"></section>
<div class="abs brand"><span class="brand-dot"></span><span class="brand-name">Pinecrest Harbor Foundation</span></div>
<nav class="abs nav">
  <a class="active">HOME</a><a>ABOUT US</a><a>SERVICES</a><a>BLOG</a><a>CONTACT US</a>
</nav>
<h1 class="abs hero-title">Non Profit<br>Organisation</h1>
<a class="abs btn-dark">READ MORE</a>
<div class="abs dots"><span></span><span></span><span class="on"></span><span></span><span></span></div>

<h2 class="abs section-title" style="top:720px">OUR MISSION</h2>
<p class="abs mission-text">There are many variations of passages of Lorem Ipsum available, but the majority have suffered alteration in some form, by injected humour, or randomised words which don't look even slightly believable. If you are going to use a passage of Lorem Ipsum, you need to be sure there isn't anything embarrassing hidden in the middle of text. All the Lorem Ipsum generators on the Internet tend to repeat predefined chunks as necessary, making this the first true generator</p>
<a class="abs btn-gold give">YOU CAN GIVE HOPE</a>

<h2 class="abs section-title" style="top:1008px">OUR STARS</h2>
<div class="abs star p1" style="left:130px;top:1079px" role="img" aria-label="Portrait of a smiling man in a black beanie"><span class="star-label">RICHARD FERANDO</span></div>
<div class="abs star p2" style="left:449px;top:1079px" role="img" aria-label="Portrait of a smiling young woman"><span class="star-label">MERRY</span></div>
<div class="abs star p3" style="left:770px;top:1079px" role="img" aria-label="Portrait of a smiling man in glasses and a red shirt"><span class="star-label">PETER MARK</span></div>
<div class="abs star p4" style="left:130px;top:1321px" role="img" aria-label="Portrait of a bald older man with glasses and a grey beard"><span class="star-label">WHITE</span></div>
<div class="abs star p5" style="left:449px;top:1321px" role="img" aria-label="Portrait of a smiling young man in a green sweater"><span class="star-label">FERANDO</span></div>
<div class="abs star p6" style="left:770px;top:1321px" role="img" aria-label="Portrait of a smiling woman in an office"><span class="star-label">JOSE</span></div>

<h2 class="abs col-title" style="left:152px;top:1621px">UPCOMING EVENTS</h2>
<div class="abs divider-v"></div>

<article class="abs event" style="top:1704px">
  <div class="date"><span class="m">NOV</span><span class="d">08</span><span class="y">2017</span></div>
  <h3>Lorem Ipsum is simply dummy text of the printing and typesetting.</h3>
  <p>Contrary to popular belief, Lorem Ipsum is not simply random text. It has roots in a piece of classical</p>
  <a class="btn-gold more">READ MORE</a>
</article>
<article class="abs event" style="top:1856px">
  <div class="date"><span class="m">NOV</span><span class="d">08</span><span class="y">2017</span></div>
  <h3>Lorem Ipsum is simply dummy text of the printing and typesetting.</h3>
  <p>Contrary to popular belief, Lorem Ipsum is not simply random text. It has roots in a piece of classical</p>
  <a class="btn-gold more">READ MORE</a>
</article>
<article class="abs event" style="top:2008px">
  <div class="date"><span class="m">NOV</span><span class="d">08</span><span class="y">2017</span></div>
  <h3>Lorem Ipsum is simply dummy text of the printing and typesetting.</h3>
  <p>Contrary to popular belief, Lorem Ipsum is not simply random text. It has roots in a piece of classical</p>
  <a class="btn-gold more">READ MORE</a>
</article>

<h2 class="abs col-title" style="left:702px;top:1621px">GET SOME HOPE IN YOUR INBOX</h2>
<div class="abs field" style="top:1680px">First Name</div>
<div class="abs field" style="top:1748px">Last Name</div>
<div class="abs field" style="top:1817px">E-mail Address</div>
<a class="abs btn-gold submit">SUBMIT</a>

<section class="abs donate" role="img" aria-label="Photo of a smiling woman resting her chin on her hands in a green park"></section>
<h2 class="abs donate-title">Help Donate</h2>
<p class="abs donate-text">There are many variations of passages of Lorem Ipsum available, but the majority have suffered alteration in some form, by injected humour, or randomised words which don't look even slightly believable.</p>
<a class="abs btn-gold donate-btn">DONATE NOW</a>

<svg class="abs wave" width="1200" height="100" viewBox="0 0 1200 100" aria-hidden="true">
  <path d="M0 60 C250 100 520 95 760 60 C930 35 1060 10 1200 40 L1200 100 L0 100 Z" fill="#c6c6c6"/>
  <path d="M0 60 C250 100 520 95 760 60 C930 35 1060 10 1200 40" fill="none" stroke="#fff" stroke-width="6"/>
</svg>

<footer class="abs footer"></footer>
<h4 class="abs foot-title" style="left:132px;top:2638px">CONTACT US</h4>
<h4 class="abs foot-title" style="left:461px;top:2638px">MENU</h4>
<h4 class="abs foot-title" style="left:615px;top:2638px">NEWSLETTER</h4>
<h4 class="abs foot-title" style="left:899px;top:2638px">FOLLOW US</h4>

<svg class="abs ico" style="top:2685px" width="12" height="16" viewBox="0 0 12 16" aria-hidden="true"><path d="M6 0C2.7 0 0 2.6 0 5.9 0 10.3 6 16 6 16s6-5.7 6-10.1C12 2.6 9.3 0 6 0zm0 8.2A2.3 2.3 0 1 1 6 3.6a2.3 2.3 0 0 1 0 4.6z" fill="#333"/></svg>
<p class="abs foot-line" style="left:172px;top:2683px">2190 Quiet Birch Lane<br>Portland, OR 97205</p>
<svg class="abs ico" style="top:2737px" width="13" height="13" viewBox="0 0 13 13" aria-hidden="true"><path d="M2.6 0.4 4.5 2.6 3.5 4.2c.9 2 2.6 3.6 4.6 4.5l1.5-1 2.2 1.9-1 2.6C6.3 12.6.4 6.7.2 1.4z" fill="#333"/></svg>
<p class="abs foot-line" style="left:172px;top:2736px">555.014.2200</p>
<svg class="abs ico" style="top:2777px" width="13" height="10" viewBox="0 0 13 10" aria-hidden="true"><path d="M0 0h13v10H0zM0 0l6.5 5L13 0" fill="#333" stroke="#c6c6c6" stroke-width=".8"/></svg>
<p class="abs foot-line" style="left:172px;top:2775px">info@pinecrestharborfoundation.com</p>

<ul class="abs menu"><li>Home</li><li>About Us</li><li>Services</li><li>Blog</li><li>Contact us</li></ul>

<div class="abs news-input">E mail id</div>
<a class="abs btn-gold signup">SIGNUP</a>

<div class="abs social" aria-label="Social links">
  <span style="background:#3b5998"></span><span style="background:#ffffff"></span><span style="background:#2a2a6a"></span><span style="background:#d9443c"></span>
</div>

<div class="abs divider-h"></div>
<p class="abs copy">Copyrights @ 2017 All Rights Reserved</p>

</body>
</html>
```